Irrigation Business needs their business cards modernised and revamped

I would like to keep my current logo, colours and revamp the format of the card.

I would like the card to be clean yet important.

Im not sure if you include texture but i would like the named logo to be indented into the card etc.

show me something alive and free something thats clinical to the point yet has a feel of achievement. i would like people to go nice card.

Target Market(s)

high end clients, corporate, sports field manger, the guys that make the decisions

Industry/Entity Type

Business

Contact Information for Business Card

nformation to be included

Dean Harlow (Director)
0487305526
dean@kolvat.biz
www.kestonfieldworks.com

instagram logo
google logo
facebook logo

Colors

Designer to choose colors to be used in the design.

Requirements
Nice to have
• indentations a really nice feel to the card good texture

```html
<!DOCTYPE html>
<html lang="en">
<head>
<meta charset="utf-8">
<title>Keston Fieldworks – Business Cards</title>
<link rel="stylesheet" href="https://fonts.googleapis.com/css2?family=Archivo:wght@400;700&family=Ubuntu:wght@400;500&display=swap">
<style>
  :root {
    --bg: #eceae7;
    --white: #ffffff;
    --brand-blue: #2a5fab;
    --sky: #2ea3d8;
    --deep: #2b66b3;
    --green: #27a35a;
  }
  html, body { margin: 0; padding: 0; overflow: hidden; }
  body {
    width: 1200px; height: 900px;
    background: var(--bg);
    position: relative;
    font-family: "Ubuntu", sans-serif;
  }
  .card {
    position: absolute;
    width: 588px; height: 362px;
    overflow: hidden;
    box-shadow: 0 6px 18px rgba(0,0,0,.18);
  }
  .card--front { left: 78px; top: 35px; background: var(--white); }
  .card--back {
    left: 388px; top: 500px;
    background: linear-gradient(135deg, var(--deep) 0%, var(--sky) 55%, var(--deep) 100%);
  }
  .card__shapes { position: absolute; inset: 0; }
  .brand {
    position: absolute; left: 0; right: 0;
    text-align: center;
    font-family: "Archivo", sans-serif;
    font-weight: 700;
    letter-spacing: .5px;
  }
  .brand__mark {
    display: block; margin: 0 auto;
    border-radius: 50%;
  }
  .card--front .brand { top: 22px; color: var(--brand-blue); font-size: 31px; }
  .card--front .brand__mark { width: 100px; height: 100px; background: var(--sky); margin-bottom: 14px; }
  .card--back .brand { top: 92px; color: var(--white); font-size: 33px; }
  .card--back .brand__mark { width: 110px; height: 110px; background: var(--white); margin-bottom: 14px; }
  .contact {
    position: absolute; left: 24px; top: 268px;
    margin: 0; padding: 0; list-style: none;
    color: var(--white); font-size: 15.5px; line-height: 22px;
  }
  .contact li { display: flex; align-items: center; gap: 6px; }
  .contact svg { width: 15px; height: 15px; flex: none; }
  .person {
    position: absolute; right: 30px; top: 252px;
    text-align: right; color: var(--white);
  }
  .person__name { font-weight: 500; font-size: 20px; margin: 0; letter-spacing: -.2px; }
  .person__role { font-size: 14.5px; margin: 2px 0 0; }
  .social { display: flex; justify-content: flex-end; gap: 6px; margin-top: 14px; }
  .social span { width: 24px; height: 24px; border-radius: 50%; background: var(--white); }
</style>
</head>
<body>

<section class="card card--front">
  <svg class="card__shapes" viewBox="0 0 588 362" aria-hidden="true">
    <defs>
      <linearGradient id="panel" x1="0" y1="0" x2="0" y2="1">
        <stop offset="0" stop-color="#2ea3d8"/>
        <stop offset="1" stop-color="#2b66b3"/>
      </linearGradient>
    </defs>
    <polygon points="0,208 390,208 372,234 0,234" fill="var(--green)"/>
    <polygon points="414,200 588,200 588,362 0,362 0,238 384,238" fill="url(#panel)"/>
  </svg>
  <div class="brand"><span class="brand__mark"></span>KESTON FIELDWORKS</div>
  <ul class="contact">
    <li><svg viewBox="0 0 16 16"><circle cx="8" cy="8" r="8" fill="#fff"/><path d="M4 6.5c0-1.5 8-1.5 8 0v1H10V6.8H6v.7H4z M5 9h6v2.5H5z" fill="#2b7cc4"/></svg>0487305526</li>
    <li><svg viewBox="0 0 16 16"><circle cx="8" cy="8" r="8" fill="#fff"/><rect x="4" y="5" width="8" height="6" fill="none" stroke="#2b7cc4" stroke-width="1.2"/><path d="M4 5l4 3.5L12 5" fill="none" stroke="#2b7cc4" stroke-width="1.2"/></svg>dean@kolvat.biz</li>
    <li><svg viewBox="0 0 16 16"><circle cx="8" cy="8" r="8" fill="#fff"/><circle cx="8" cy="8" r="4" fill="none" stroke="#2b7cc4" stroke-width="1.2"/><path d="M4 8h8M8 4v8" stroke="#2b7cc4" stroke-width="1"/></svg>www.kestonfieldworks.com</li>
  </ul>
  <div class="person">
    <p class="person__name">DEAN HARLOW</p>
    <p class="person__role">Director</p>
    <div class="social"><span></span><span></span><span></span></div>
  </div>
</section>

<section class="card card--back">
  <div class="brand"><span class="brand__mark"></span>KESTON FIELDWORKS</div>
</section>

</body>
</html>
```